Website for Briar Hollow Gathering Church

Wordpress website design required for Briar Hollow Gathering Church. We are a family oriented church catering for age groups from school age to elderly people. The church has a wide variety of activities which it coordinates. The idea is to describe the activities on the activities page, but cross-link them to show which would be applicable to the different age groups.

We would like an inviting website which is easy to read and navigate.

Target Market(s)

Very wide audience - from school age youth to elderly people, so design and style should cater for both audiences.

Industry/Entity Type

Church

Coding

Coded - Design and coding required

Number of Pages Required

5+ page

Font styles to use
Sans Serif

Colors
0255a3
ffffff
0792cd
f78f20

Requirements
Must have
• Inviting website.
• Clear readable font.
• Space to import photos to balance text on each page.
• Need to project a dynamic and progressive feel for the church.
• Easy to navigate.
Nice to have
• Scrolling photos on pages. Ability to enter questions/ comments/prayer requests on Home page.
Should not have
• Conservative audience, so should not be too bold.

```html
<!DOCTYPE html>
<html lang="en">
<head>
<meta charset="utf-8">
<title>Briar Hollow Gathering Church</title>
<link rel="stylesheet" href="https://fonts.googleapis.com/css2?family=Open+Sans:ital,wght@0,400;0,600;0,700;0,800;1,600;1,700&display=swap">
<style>
:root{
  --blue:#0255a3;
  --blue-deep:#0a3f8c;
  --blue-light:#0792cd;
  --orange:#f78f20;
  --white:#ffffff;
  --ink:#3d3d3d;
  --grey-bg:#efefef;
  --line:#d9d9d9;
}
*{box-sizing:border-box;margin:0;padding:0}
html,body{width:1200px;height:2359px;overflow:hidden}
body{font-family:"Open Sans",Arial,sans-serif;color:var(--ink);background:var(--white);position:relative}
a{color:inherit;text-decoration:none}
.abs{position:absolute}

/* header */
.site-header{position:absolute;left:0;top:0;width:1200px;height:137px;background:var(--white)}
.brand{position:absolute;left:74px;top:88px;display:flex;align-items:center;gap:8px;color:var(--blue);font-weight:700;font-size:19px}
.brand-dot{width:12px;height:12px;border-radius:50%;background:var(--blue)}
.partner{position:absolute;left:771px;top:56px;display:flex;align-items:center;gap:12px;color:var(--ink);font-weight:600;font-size:18px}
.partner-dot{width:46px;height:46px;border-radius:50%;border:3px solid var(--ink)}

/* nav */
.main-nav{position:absolute;left:0;top:137px;width:1200px;height:55px;background:linear-gradient(#1d73c4,#0a55a6)}
.main-nav ul{list-style:none;display:flex;height:55px;padding-left:74px}
.main-nav li{height:55px;line-height:55px;font-size:13.5px;font-weight:700;color:var(--white);padding:0 18px;text-transform:uppercase}
.main-nav li.active{background:var(--orange);padding:0 16px}
.main-nav li+li{margin-left:16px}
.nav-search{position:absolute;left:1104px;top:16px}

/* hero */
.hero{position:absolute;left:0;top:192px;width:1200px;height:469px;background:linear-gradient(135deg,#6f8a4a 0%,#a9b08b 35%,#c9c2b4 55%,#8a6d52 80%,#5b6e3d 100%)}
.hero-bar{position:absolute;left:0;bottom:0;width:1200px;height:67px;background:rgba(0,0,0,.72)}
.hero-title{position:absolute;left:74px;top:11px;font-size:41px;font-weight:800;color:var(--white);letter-spacing:.5px}
.hero-arrows{position:absolute;left:1064px;top:19px;display:flex;gap:14px}

/* welcome */
.welcome{position:absolute;left:0;top:661px;width:1200px;height:333px;background:linear-gradient(#ffffff 45%,#ececec);text-align:center}
.section-title{color:var(--blue);font-weight:700;font-size:24px;text-transform:uppercase}
.welcome .section-title{margin-top:48px}
.welcome p{width:1040px;margin:20px auto 0;font-size:15.5px;line-height:28.5px}
.btn{display:inline-block;background:var(--orange);color:var(--white);font-weight:700;font-size:14.5px;text-transform:uppercase;text-align:center;border-radius:2px}
.welcome .btn{position:absolute;left:524px;top:243px;width:152px;height:48px;line-height:48px}

/* message + prayer */
.message-band{position:absolute;left:0;top:994px;width:1200px;height:261px;background:var(--white)}
.minister{position:absolute;left:74px;top:42px;width:692px;height:178px;border:1px solid var(--line);box-shadow:0 1px 3px rgba(0,0,0,.08);padding:20px 17px}
.minister .section-title{text-align:left}
.minister blockquote{margin-top:12px;font-style:italic;font-weight:700;font-size:16px;line-height:28px;color:var(--ink)}
.minister cite{display:block;margin-top:8px;font-size:14px;font-weight:600;color:var(--orange)}
.prayer{position:absolute;left:794px;top:42px;width:332px;height:178px;background:linear-gradient(#0c7ccc,#2a9fe2);padding:20px 18px}
.prayer .section-title{color:var(--white)}
.field{display:block;background:var(--white);height:41px;line-height:41px;padding-left:16px;font-size:11.5px;font-weight:600;color:#9a9a9a;text-transform:uppercase}
.prayer .field{margin-top:14px;width:295px}
.prayer .btn{position:absolute;left:162px;top:114px;width:151px;height:47px;line-height:47px}

/* news */
.news{position:absolute;left:0;top:1255px;width:1200px;height:422px;background:var(--grey-bg)}
.news .section-title{position:absolute;left:75px;top:37px}
.news-arrows{position:absolute;left:1084px;top:42px;display:flex;gap:12px}
.news-card{position:absolute;top:91px;width:331px}
.news-photo{width:331px;height:183px}
.news-card h3{margin-top:14px;font-size:19.5px;line-height:28px;font-weight:600;color:var(--ink)}
.read-more{display:flex;align-items:center;gap:6px;margin-top:10px;font-size:14px;font-weight:600;color:var(--orange)}

/* theme + service */
.theme{position:absolute;left:0;top:1677px;width:1200px;height:368px;background:var(--white)}
.theme .section-title.t{position:absolute;left:75px;top:34px}
.theme-photo{position:absolute;left:75px;top:96px;width:266px;height:220px;background:linear-gradient(#e7e6e2 0%,#9a8f86 35%,#4a3c35 70%,#2b2220 100%)}
.theme-text{position:absolute;left:371px;top:97px;width:400px;font-size:16px;line-height:26px}
.theme .btn{position:absolute;left:371px;top:269px;width:151px;height:47px;line-height:47px}
.services{position:absolute;left:794px;top:41px;width:332px;height:275px;border:2px solid #e3e3e3;padding:16px 17px}
.service{border-bottom:1px solid #e2e2e2;padding:8px 0 9px}
.service:last-child{border-bottom:none}
.service h4{font-size:15px;font-weight:700;color:var(--orange)}
.service-meta{display:flex;justify-content:space-between;margin-top:6px;font-size:13px;color:var(--ink)}
.service-meta span{display:flex;align-items:center;gap:6px}
.services .section-title{margin-bottom:4px}

/* footer */
.site-footer{position:absolute;left:0;top:2045px;width:1200px;height:257px;background:linear-gradient(#0c46a0,#1d64cf);color:var(--white)}
.foot-col{position:absolute;top:45px}
.foot-col h5{font-size:14.5px;font-weight:700;text-transform:uppercase;margin-bottom:10px}
.foot-col p,.foot-col li{font-size:13.5px;line-height:23px}
.foot-col ul{list-style:none}
.foot-col .hl{color:var(--orange);font-weight:700}
.foot-col strong{display:block;margin-top:11px;font-weight:700}
.signup{display:flex;margin-top:2px}
.signup .field{width:219px;height:40px;line-height:40px;font-size:11px}
.signup .btn{width:75px;height:40px;line-height:40px;font-size:12.5px;border-radius:0}
.social{display:flex;gap:18px;margin-top:14px}
.social span{width:19px;height:19px;border-radius:3px;background:var(--white)}
.legal{position:absolute;left:0;top:2302px;width:1200px;height:57px;background:var(--blue-deep);color:var(--white);text-align:center;line-height:57px;font-size:12px}
</style>
</head>
<body>

<header class="site-header">
  <div class="brand"><span class="brand-dot"></span>Briar Hollow Gathering Church</div>
  <div class="partner"><span class="partner-dot"></span>Gathering Church Network</div>
</header>

<nav class="main-nav">
  <ul>
    <li class="active">Home</li>
    <li>Age Group</li>
    <li>Activities</li>
    <li>Events Calender</li>
    <li>About</li>
    <li>Contact Us</li>
  </ul>
  <svg class="nav-search" width="22" height="22" viewBox="0 0 22 22" aria-label="Search"><circle cx="9" cy="9" r="6.5" fill="none" stroke="#fff" stroke-width="3"/><line x1="14" y1="14" x2="20" y2="20" stroke="#fff" stroke-width="3.5" stroke-linecap="round"/></svg>
</nav>

<section class="hero" role="img" aria-label="Photo of the men's coffee group chatting with cups in a garden courtyard">
  <div class="hero-bar">
    <h1 class="hero-title">MENS COFFEE GROUP</h1>
    <div class="hero-arrows">
      <svg width="24" height="30" viewBox="0 0 24 30"><polyline points="17,4 7,15 17,26" fill="none" stroke="#fff" stroke-width="4.5"/></svg>
      <svg width="24" height="30" viewBox="0 0 24 30"><polyline points="7,4 17,15 7,26" fill="none" stroke="#f78f20" stroke-width="4.5"/></svg>
    </div>
  </div>
</section>

<section class="welcome">
  <h2 class="section-title">Welcome to our website</h2>
  <p>Aliquam molestie, mi et imperdiet euismod, dui purus auctor tellus, et interdum lacus lectus et ante. Sed accumsan sollicitudin sapien, sit amet adipiscing turpis gravida ac. In congue, neque ac lobortis volutpat, libero mauris varius mi, vitae suscipit ipsum ligula vitae risus. Duis aliquam nibh a dui iaculis viverra id a velit. Vivamus egestas risus in magna varius commodo. Sed semper viverra egestas.<br>Etiam pretium porttitor lectus, vel ornare neque porta volutpat.</p>
  <a class="btn" href="#">Read More</a>
</section>

<section class="message-band">
  <article class="minister">
    <h2 class="section-title">Minister's Weekly Message</h2>
    <blockquote>“ Aliquam molestie, mi et imperdiet euismod, dui purus auctor tellus, et interdum lacus lectus et ante. Sed accumsan sollicitudin sapien...”</blockquote>
    <cite>-Name Heading</cite>
  </article>
  <form class="prayer">
    <h2 class="section-title">Prayer Request</h2>
    <span class="field">Enter Email Address</span>
    <a class="btn" href="#">Send Request</a>
  </form>
</section>

<section class="news">
  <h2 class="section-title">Latest News</h2>
  <div class="news-arrows">
    <svg width="16" height="22" viewBox="0 0 16 22"><polyline points="12,3 4,11 12,19" fill="none" stroke="#777" stroke-width="3"/></svg>
    <svg width="16" height="22" viewBox="0 0 16 22"><polyline points="4,3 12,11 4,19" fill="none" stroke="#777" stroke-width="3"/></svg>
  </div>
  <article class="news-card" style="left:75px">
    <div class="news-photo" role="img" aria-label="Photo of families sharing a meal in the church hall" style="background:linear-gradient(135deg,#6b5a4a,#c9b9a6 50%,#7a3b32)"></div>
    <h3>Aliquam molestie, mi et imperdiet euismod, dui purus auctor</h3>
    <a class="read-more" href="#">Read More <svg width="9" height="9" viewBox="0 0 9 9"><polyline points="1,1 4,4.5 1,8" fill="none" stroke="#f78f20" stroke-width="1.6"/><polyline points="5,1 8,4.5 5,8" fill="none" stroke="#f78f20" stroke-width="1.6"/></svg></a>
  </article>
  <article class="news-card" style="left:436px">
    <div class="news-photo" role="img" aria-label="Photo of children lighting candles on a red altar cloth" style="background:linear-gradient(135deg,#8a7d6e,#b8322e 55%,#3b2f3a)"></div>
    <h3>Aliquam molestie, mi et imperdiet euismod, dui purus auctor</h3>
    <a class="read-more" href="#">Read More <svg width="9" height="9" viewBox="0 0 9 9"><polyline points="1,1 4,4.5 1,8" fill="none" stroke="#f78f20" stroke-width="1.6"/><polyline points="5,1 8,4.5 5,8" fill="none" stroke="#f78f20" stroke-width="1.6"/></svg></a>
  </article>
  <article class="news-card" style="left:796px">
    <div class="news-photo" role="img" aria-label="Photo of a community lunch with food laid out on tables" style="background:linear-gradient(135deg,#cfc9bd,#8a6a52 50%,#c8b042)"></div>
    <h3>Aliquam molestie, mi et imperdiet euismod, dui purus auctor</h3>
    <a class="read-more" href="#">Read More <svg width="9" height="9" viewBox="0 0 9 9"><polyline points="1,1 4,4.5 1,8" fill="none" stroke="#f78f20" stroke-width="1.6"/><polyline points="5,1 8,4.5 5,8" fill="none" stroke="#f78f20" stroke-width="1.6"/></svg></a>
  </article>
</section>

<section class="theme">
  <h2 class="section-title t">Theme of Church</h2>
  <div class="theme-photo" role="img" aria-label="Photo of a congregation seated in the church hall"></div>
  <p class="theme-text">Aliquam molestie, mi et imperdiet euismod, dui purus auctor tellus, et interdum lacus lectus et ante.<br>Sed accumsan sollicitudin sapien, sit amet adipiscing turpis gravida ac. In congue, neque ac lobortis volutpat, libero mauris varius mi. Aliquam molestie, mi et imperdiet euismoddum lacus lectus et ante.</p>
  <a class="btn" href="#">Read More</a>

  <aside class="services">
    <h2 class="section-title">Service Times</h2>
    <div class="service">
      <h4>Vestibulum ante</h4>
      <div class="service-meta"><span><svg width="11" height="11" viewBox="0 0 11 11"><rect x=".5" y="1.5" width="10" height="9" fill="none" stroke="#555"/><rect x=".5" y="1.5" width="10" height="2.5" fill="#555"/></svg>7:00 am to 10: am</span><span><svg width="11" height="11" viewBox="0 0 11 11"><rect x=".5" y="1.5" width="10" height="9" fill="none" stroke="#555"/><rect x=".5" y="1.5" width="10" height="2.5" fill="#555"/></svg>Oct 29, 2016</span></div>
    </div>
    <div class="service">
      <h4>Vestibulum ante</h4>
      <div class="service-meta"><span><svg width="11" height="11" viewBox="0 0 11 11"><rect x=".5" y="1.5" width="10" height="9" fill="none" stroke="#555"/><rect x=".5" y="1.5" width="10" height="2.5" fill="#555"/></svg>7:00 am to 10: am</span><span><svg width="11" height="11" viewBox="0 0 11 11"><rect x=".5" y="1.5" width="10" height="9" fill="none" stroke="#555"/><rect x=".5" y="1.5" width="10" height="2.5" fill="#555"/></svg>Oct 29, 2016</span></div>
    </div>
    <div class="service">
      <h4>Vestibulum ante</h4>
      <div class="service-meta"><span><svg width="11" height="11" viewBox="0 0 11 11"><rect x=".5" y="1.5" width="10" height="9" fill="none" stroke="#555"/><rect x=".5" y="1.5" width="10" height="2.5" fill="#555"/></svg>7:00 am to 10: am</span><span><svg width="11" height="11" viewBox="0 0 11 11"><rect x=".5" y="1.5" width="10" height="9" fill="none" stroke="#555"/><rect x=".5" y="1.5" width="10" height="2.5" fill="#555"/></svg>Oct 29, 2016</span></div>
    </div>
  </aside>
</section>

<footer class="site-footer">
  <div class="foot-col" style="left:74px;width:250px">
    <h5>About Us</h5>
    <p>Duis aliquam nibh a dui iaculis viverra id a velit. Vivamus egestas risus in magna varius commodo. Sed semper viverra egestas. Aenean a nibh eget turpis vehicula tempus ac sed massa.</p>
  </div>
  <div class="foot-col" style="left:382px">
    <h5>Site Map</h5>
    <ul><li>Home</li><li>Age Group</li><li>Activities</li><li>Events Calender</li><li>About</li><li>Contact Us</li></ul>
  </div>
  <div class="foot-col" style="left:550px">
    <h5>Contact Info</h5>
    <p class="hl">Briar Hollow Gathering Church</p>
    <p>14 Fernleigh Lane, Briar Hollow,<br>6021 Australia</p>
    <strong>Get Map Direction</strong>
  </div>
  <div class="foot-col" style="left:832px">
    <h5>Email Sign Up</h5>
    <div class="signup"><span class="field">Enter Email Address</span><a class="btn" href="#">Sign Up</a></div>
    <h5 style="margin-top:38px">Follow Us</h5>
    <div class="social"><span></span><span></span><span></span><span></span><span></span></div>
  </div>
</footer>
<div class="legal">Copyright © 2016. Company Name. All Right Reserved</div>

</body>
</html>
```